Professional & attention grabbing.

A business card design, front and back. I already have a logo I will attach, but I am open to something new as well.
Things to include:
Name:
Title:
Phone:
Email:
Wanting something that is professional but attention grabbing.
Also we do a lot of work using drones on natural gas pipelines (leading the future)if you want to include any of that. I'm open to ideas.
Target Market(s)
Natural gas transmission industry / greenhouse gas mitigation industry
Industry/Entity Type
Business
Colors
Designer to choose colors to be used in the design.
Look and feel
Each slider illustrates characteristics of the customer's brand and the style your logo design should communicate.

```html
<!DOCTYPE html>
<html lang="en">
<head>
<meta charset="utf-8">
<title>Kestrel Inspections – Business Card</title>
<link rel="stylesheet" href="https://fonts.googleapis.com/css2?family=Roboto:wght@400;500;700&display=swap">
<style>
  :root {
    --page-bg: #e9e7e5;
    --card-bg: #161616;
    --brand-red: #c1272d;
    --brand-grey: #cfcfcf;
    --text-white: #f2f2f2;
    --text-muted: #8d8d8d;
    --divider: #5a5a5a;
  }
  * { margin: 0; padding: 0; box-sizing: border-box; }
  html, body {
    width: 1200px;
    height: 864px;
    overflow: hidden;
    background: var(--page-bg);
    font-family: "Roboto", Arial, sans-serif;
  }
  .canvas {
    width: 1200px;
    height: 864px;
    display: flex;
    align-items: center;
    justify-content: center;
    gap: 48px;
  }
  .card {
    width: 528px;
    height: 302px;
    background: var(--card-bg);
    border-radius: 4px;
    position: relative;
    overflow: hidden;
  }

  /* Back side */
  .card-back .brand-block {
    position: absolute;
    left: 150px;
    top: 56px;
    display: flex;
    flex-direction: column;
    align-items: center;
    gap: 20px;
  }
  .card-back .brand-square {
    width: 120px;
    height: 120px;
    background: var(--brand-red);
  }
  .card-back .brand-name {
    font-weight: 700;
    font-size: 30px;
    color: var(--brand-grey);
    letter-spacing: 1px;
  }
  .card-back .site-url {
    position: absolute;
    left: 58px;
    top: 60px;
    writing-mode: vertical-rl;
    transform: rotate(180deg);
    font-size: 12px;
    letter-spacing: 4px;
    color: var(--text-muted);
  }

  /* Front side */
  .card-front .brand-block {
    position: absolute;
    left: 40px;
    top: 112px;
    display: flex;
    align-items: center;
    gap: 12px;
  }
  .card-front .brand-square {
    width: 44px;
    height: 44px;
    background: var(--brand-red);
  }
  .card-front .brand-name {
    font-weight: 700;
    font-size: 22px;
    line-height: 1.05;
    color: var(--text-white);
  }
  .card-front .divider {
    position: absolute;
    left: 274px;
    top: 96px;
    width: 1px;
    height: 110px;
    background: var(--divider);
  }
  .contact {
    position: absolute;
    left: 294px;
    top: 94px;
  }
  .contact .person-name {
    font-size: 17px;
    font-weight: 500;
    color: var(--brand-red);
  }
  .contact .person-title {
    font-size: 15px;
    color: var(--text-white);
    margin-bottom: 10px;
  }
  .contact-list { list-style: none; }
  .contact-list li {
    display: flex;
    align-items: center;
    gap: 10px;
    font-size: 13px;
    color: var(--text-white);
    margin-bottom: 6px;
  }
  .contact-list svg { width: 13px; height: 13px; flex: none; }
</style>
</head>
<body>
<main class="canvas">

  <section class="card card-back" aria-label="Card back">
    <div class="site-url">www.kestrelinspect.com</div>
    <div class="brand-block">
      <div class="brand-square"></div>
      <div class="brand-name">Kestrel Inspections</div>
    </div>
  </section>

  <section class="card card-front" aria-label="Card front">
    <div class="brand-block">
      <div class="brand-square"></div>
      <div class="brand-name">Kestrel<br>Inspections</div>
    </div>
    <div class="divider"></div>
    <div class="contact">
      <div class="person-name">Alex Marlow</div>
      <div class="person-title">President</div>
      <ul class="contact-list">
        <li>
          <svg viewBox="0 0 16 16" aria-hidden="true"><path fill="var(--brand-red)" d="M3 1h3l1.5 4-2 1.3a9 9 0 0 0 4.2 4.2l1.3-2 4 1.5v3a2 2 0 0 1-2 2A13 13 0 0 1 1 3a2 2 0 0 1 2-2z"/></svg>
          555 0142 7788
        </li>
        <li>
          <svg viewBox="0 0 16 16" aria-hidden="true"><rect x="1" y="3" width="14" height="10" rx="1" fill="var(--brand-red)"/><path d="M1.5 3.8 8 9l6.5-5.2" stroke="var(--card-bg)" stroke-width="1.4" fill="none"/></svg>
          alex@kestrelinspect.com
        </li>
        <li>
          <svg viewBox="0 0 16 16" aria-hidden="true"><circle cx="8" cy="8" r="7" fill="var(--brand-red)"/><path d="M1 8h14M8 1c3 3 3 11 0 14M8 1c-3 3-3 11 0 14" stroke="var(--card-bg)" stroke-width="1.1" fill="none"/></svg>
          www.kestrelinspect.com
        </li>
      </ul>
    </div>
  </section>

</main>
</body>
</html>
```